Business Card Design Project

Doctor, Pain Management. Need a new business card design with appointment info on the back. New address is 18 Corvell Road, Suite 304, Brisdale, NJ 07391. Right now I believe the rest of the information is staying the same.

```html
<!DOCTYPE html>
<html lang="en">
<head>
<meta charset="utf-8">
<title>Steady Relief Pain Care – Business Card</title>
<link rel="stylesheet" href="https://fonts.googleapis.com/css2?family=Noto+Serif:wght@400;700&display=swap">
<style>
  :root{
    --stage:#2b2b2d;
    --card-white:#f4f4f2;
    --ink-dark:#2a2922;
    --ink-text:#1d1c18;
    --muted:#b9b7ae;
    --yellow-front:#e6dc57;
    --yellow-band:#e8c60a;
    --accent-orange:#d08a2c;
    --figure-a:#3a3b44;
    --figure-b:#a5502a;
  }
  *{box-sizing:border-box;margin:0;padding:0}
  html,body{width:1200px;height:923px;overflow:hidden;background:var(--stage)}
  body{font-family:"Noto Serif",Georgia,serif;color:var(--ink-text);position:relative}

  .card{position:absolute;left:337px;width:526px;height:300px;overflow:hidden;
        box-shadow:0 10px 28px rgba(0,0,0,.45)}

  /* Appointment side */
  .card-back{top:110px;background:var(--card-white)}
  .appt-title{position:absolute;top:30px;width:100%;text-align:center;font-size:27px;font-weight:400;letter-spacing:.5px}
  .appt-note{position:absolute;top:78px;width:100%;text-align:center;font-size:15px;line-height:1.3}
  .appt-field{position:absolute;font-size:16px;display:flex;align-items:flex-end;gap:6px}
  .appt-field .line{display:block;border-bottom:1px solid var(--ink-text);height:1px;margin-bottom:4px}
  .field-for{left:34px;top:136px}
  .field-time{left:300px;top:136px}
  .field-date{left:34px;top:170px}
  .days{position:absolute;left:34px;top:206px;display:flex;gap:22px;font-size:16px}
  .day{display:flex;align-items:center;gap:6px}
  .day .box{width:13px;height:13px;border:1px solid var(--ink-text);display:inline-block}
  .back-band{position:absolute;left:0;bottom:0;width:100%;height:58px;background:var(--yellow-band);
             padding:9px 0 0 34px;font-size:14px;line-height:1.35;color:#4a3f10}

  /* Front side */
  .card-front{top:490px;background:var(--card-white)}
  .front-shapes{position:absolute;inset:0}
  .spine-visual{position:absolute;left:18px;top:70px;width:70px;height:92px;border-radius:3px;
                background:radial-gradient(ellipse at 55% 62%,var(--figure-b) 0%,var(--figure-a) 60%,#24252b 100%)}
  .practice-name{position:absolute;left:36px;top:102px;font-size:21px;font-weight:700;color:#fff;
                 white-space:nowrap}
  .doctor{position:absolute;left:24px;top:196px;color:#fff}
  .doctor-name{font-size:18px;font-weight:700;white-space:nowrap}
  .doctor-cred{font-size:12px;color:var(--muted);margin-left:12px;margin-top:-2px}
  .contact-list{position:absolute;right:12px;top:130px;list-style:none;text-align:right;font-size:12px;line-height:18px}
  .contact-list li{display:flex;justify-content:flex-end;align-items:center;gap:5px;white-space:nowrap}
  .contact-list .icon{width:14px;height:14px;background:#111;display:inline-flex;align-items:center;justify-content:center}
  .address{position:absolute;right:12px;bottom:14px;font-size:12.5px;white-space:nowrap}
</style>
</head>
<body>

<section class="card card-back" aria-label="Appointment card, back side">
  <h2 class="appt-title">Appoinment</h2>
  <p class="appt-note">If you are unable to keep your appointment,<br>please contact us as soon as posible.</p>
  <div class="appt-field field-for">For: <span class="line" style="width:220px"></span></div>
  <div class="appt-field field-time">Time: <span class="line" style="width:150px"></span></div>
  <div class="appt-field field-date">Date: <span class="line" style="width:410px"></span></div>
  <div class="days">
    <span class="day"><span class="box"></span>Mon</span>
    <span class="day"><span class="box"></span>Tue</span>
    <span class="day"><span class="box"></span>Wed</span>
    <span class="day"><span class="box"></span>Thu</span>
    <span class="day"><span class="box"></span>Fri</span>
  </div>
  <div class="back-band">(973) 555-0148<br>(973) 555-0163</div>
</section>

<section class="card card-front" aria-label="Business card, front side">
  <svg class="front-shapes" viewBox="0 0 526 300" width="526" height="300" aria-hidden="true">
    <path d="M485 0 H526 V300 H20 Q400 250 485 0 Z" fill="var(--yellow-front)"/>
    <path d="M485 0 Q400 250 20 300" fill="none" stroke="var(--accent-orange)" stroke-width="2"/>
    <path d="M0 0 H400 Q330 230 10 300 H0 Z" fill="var(--ink-dark)"/>
  </svg>
  <div class="spine-visual" role="img" aria-label="Photo of a person's back with the spine highlighted in pain"></div>
  <h1 class="practice-name">Steady Relief Pain Care</h1>
  <div class="doctor">
    <div class="doctor-name">Dr. Lorin Vashe</div>
    <div class="doctor-cred">M.D., Ph.D.</div>
  </div>
  <ul class="contact-list">
    <li>(973) 555-0148
      <span class="icon"><svg width="10" height="10" viewBox="0 0 10 10"><path d="M2 1 L4 1 L4.6 3 L3.5 4 Q4.5 6 6 6.5 L7 5.4 L9 6 L9 8 Q5 9 2 5.5 Q1 3 2 1Z" fill="#f4f4f2"/></svg></span></li>
    <li>(973) 555-0163
      <span class="icon"><svg width="10" height="10" viewBox="0 0 10 10"><rect x="1.5" y="2" width="7" height="6" fill="none" stroke="#f4f4f2"/><path d="M3 4 H7 M3 6 H7" stroke="#f4f4f2"/></svg></span></li>
    <li>www.steadyreliefpc.com
      <span class="icon"><svg width="10" height="10" viewBox="0 0 10 10"><circle cx="5" cy="5" r="3.8" fill="none" stroke="#f4f4f2"/><path d="M1.2 5 H8.8 M5 1.2 V8.8" stroke="#f4f4f2" stroke-width=".8"/></svg></span></li>
    <li>office@steadyreliefpc.com
      <span class="icon"><svg width="10" height="10" viewBox="0 0 10 10"><rect x="1" y="2.5" width="8" height="5.5" fill="none" stroke="#f4f4f2"/><path d="M1 2.5 L5 6 L9 2.5" fill="none" stroke="#f4f4f2"/></svg></span></li>
  </ul>
  <p class="address">18 Corvell Road, Suite 304, Brisdale, NJ 07391</p>
</section>

</body>
</html>
```